BOLD & MINIMALIST DESIGN NEEDED

We want a very bold but minimalistic business card design that is impactful and utilizes both sides of the business card. Our current logo is included for your use.

We want bold fonts and good use of negative space. We don't want the logo to overpower the design.

Target Market(s)

Professionals who are building new commercial buildings.

Industry/Entity Type

Construction

Contact Information for Business Card

Name, Title, email, office phone, cell phone, website

Font styles to use
Serif
Sans Serif

Requirements
Must have
• Bold design!

```html
<!DOCTYPE html>
<html lang="en">
<head>
<meta charset="utf-8">
<title>Ridgeline Design + Build — Business Card</title>
<link rel="stylesheet" href="https://fonts.googleapis.com/css2?family=Montserrat:wght@500;800&family=Poppins:wght@400&display=swap">
<style>
  :root {
    --stage: #1c1d1f;
    --card-black: #0b0c0e;
    --white: #f4f4f2;
    --green-deep: #86c22a;
    --green-light: #b9de86;
    --ink: #0b0c0e;
  }
  * { box-sizing: border-box; margin: 0; padding: 0; }
  html, body {
    width: 1200px; height: 1015px; overflow: hidden;
    background: var(--stage);
  }
  .stage { position: relative; width: 1200px; height: 1015px; }
  .card {
    position: absolute; width: 560px; height: 320px;
    box-shadow: 0 18px 40px rgba(0,0,0,.55);
    overflow: hidden;
  }
  /* Front side */
  .card--front {
    left: 100px; top: 110px;
    background: var(--card-black);
    display: flex; flex-direction: column; align-items: center; justify-content: center;
  }
  .brand { display: flex; align-items: center; gap: 14px; }
  .brand__square { width: 30px; height: 30px; background: var(--green-deep); }
  .brand__name {
    font-family: "Montserrat", sans-serif; font-weight: 800;
    font-size: 46px; letter-spacing: 1px; color: var(--white);
  }
  .brand__rule { width: 330px; height: 1px; background: var(--white); margin: 8px 0 6px; }
  .brand__tagline {
    font-family: "Montserrat", sans-serif; font-weight: 500;
    font-size: 14px; letter-spacing: 9px; color: var(--white);
  }
  /* Back side */
  .card--back {
    left: 540px; top: 580px;
    background: linear-gradient(160deg, var(--green-deep) 0%, var(--green-light) 70%);
  }
  .identity { position: absolute; left: 36px; top: 58px; }
  .identity__name {
    font-family: "Montserrat", sans-serif; font-weight: 800;
    font-size: 24px; color: var(--ink); letter-spacing: .5px;
    padding-bottom: 4px; border-bottom: 1.5px solid var(--ink);
  }
  .identity__title {
    font-family: "Montserrat", sans-serif; font-weight: 500;
    font-size: 12px; color: var(--ink); letter-spacing: .5px; margin-top: 5px;
  }
  .contact { position: absolute; left: 36px; bottom: 32px; list-style: none; }
  .contact__item {
    display: flex; align-items: center; gap: 8px;
    font-family: "Poppins", sans-serif; font-size: 14px; line-height: 22px; color: var(--ink);
  }
  .contact__item svg { width: 14px; height: 14px; flex: none; }
  .accent-block {
    position: absolute; right: 0; top: 70px;
    width: 200px; height: 200px; background: var(--ink);
  }
</style>
</head>
<body>
<main class="stage">
  <section class="card card--front" aria-label="Card front">
    <div class="brand">
      <span class="brand__square"></span>
      <span class="brand__name">RIDGELINE</span>
    </div>
    <div class="brand__rule"></div>
    <div class="brand__tagline">DESIGN + BUILD</div>
  </section>

  <section class="card card--back" aria-label="Card back">
    <div class="identity">
      <div class="identity__name">MARCUS HALE</div>
      <div class="identity__title">MANAGING DIRECTOR</div>
    </div>
    <ul class="contact">
      <li class="contact__item">
        <svg viewBox="0 0 24 24" fill="none" stroke="currentColor" stroke-width="2.4"><path d="M5 3h4l2 5-3 2a12 12 0 0 0 6 6l2-3 5 2v4a2 2 0 0 1-2 2A18 18 0 0 1 3 5a2 2 0 0 1 2-2z"/></svg>
        044-555 210 347
      </li>
      <li class="contact__item">
        <svg viewBox="0 0 24 24" fill="none" stroke="currentColor" stroke-width="2.4"><rect x="6" y="2" width="12" height="20" rx="2"/><line x1="11" y1="18" x2="13" y2="18"/></svg>
        044-555 918 462
      </li>
      <li class="contact__item">
        <svg viewBox="0 0 24 24" fill="currentColor"><path d="M2 5h20v14H2z"/><path d="M2 5l10 8 10-8" fill="none" stroke="#b9de86" stroke-width="2"/></svg>
        info@ridgelinebuild.com
      </li>
      <li class="contact__item">
        <svg viewBox="0 0 24 24" fill="none" stroke="currentColor" stroke-width="2"><circle cx="12" cy="12" r="10"/><path d="M2 12h20M12 2c3 3 3 17 0 20M12 2c-3 3-3 17 0 20"/></svg>
        www.ridgelinebuild.com
      </li>
    </ul>
    <div class="accent-block"></div>
  </section>
</main>
</body>
</html>
```